Bicycle Tour Schedule on a Business Card

Need to develop a 2 side business card that highlights a series of bike tours on 1 side and a series of events on the other side.
This will be inserted into a card wallet that attaches to a cell phone and will be handed out at an expo. The card wallets are black and red so color must coordinate with both. There is a photo of the card wallets attached.

1 side needs to be devoted to Pedal Vista Trek and the others to KQR Venture events on the other. Dates and websites are very important.

Target Market(s)

Cyclists
Predominantly men ages 40+
Educated, Professionals

Industry/Entity Type

Business

Font styles to use
Serif

Requirements
Must have
• Pedal vista treks logo on 1 side and KQR Venture logo on the other side
• dates and websites clearly visible
• Design of both sides must go together.
• Must be portrait not landscape

```html
<!DOCTYPE html>
<html lang="en">
<head>
<meta charset="utf-8">
<title>Pedal Vista Treks &amp; KQR Venture – Event Cards</title>
<link rel="stylesheet" href="https://fonts.googleapis.com/css2?family=Source+Sans+3:ital,wght@0,400;0,600;0,700;1,700&display=swap">
<style>
  :root {
    --backdrop: #8f9292;
    --paper: #f2f2f0;
    --tour-blue: #0d4fa3;
    --tour-green: #3aa35a;
    --event-red: #b5122e;
    --event-blue: #2a8fc1;
    --ink: #3a3a3a;
    --ink-strong: #2a2a2a;
  }
  * { box-sizing: border-box; margin: 0; padding: 0; }
  html, body {
    width: 1105px; height: 1200px; overflow: hidden;
    background: var(--backdrop);
    font-family: "Source Sans 3", "Myriad Pro", Arial, sans-serif;
  }
  .card-pair {
    position: absolute; top: 266px; left: 104px;
    display: flex; gap: 84px;
  }
  .card {
    position: relative; width: 408px; height: 700px;
    background: var(--paper); overflow: hidden;
  }
  .card__edge { position: absolute; inset: 0; width: 408px; height: 700px; }
  .card__content {
    position: absolute; right: 46px; left: 60px;
    text-align: right; color: var(--ink);
  }
  .card--tours .card__content { top: 268px; }
  .card--events .card__content { top: 242px; }

  .brand-name {
    position: absolute; right: 46px; font-weight: 700; line-height: 1.05;
    text-align: right; white-space: nowrap;
  }
  .brand-name--tours { top: 92px; font-size: 38px; color: var(--tour-blue); }
  .brand-mark {
    position: absolute; top: 30px; right: 48px; width: 112px; height: 112px;
    background: var(--event-red);
  }
  .brand-name--events { top: 166px; font-size: 32px; color: var(--event-red); }

  .tagline { font-style: italic; font-weight: 700; white-space: nowrap; }
  .tagline--tours { color: var(--tour-blue); font-size: 20px; line-height: 26px; }
  .tagline--events { color: var(--event-red); font-size: 21px; line-height: 31px; }

  .listing { list-style: none; }
  .listing__name { display: block; font-weight: 400; }
  .listing__detail { display: block; font-weight: 600; color: var(--ink-strong); }
  .listing__item { white-space: nowrap; }

  .listing--tours { margin-top: 34px; }
  .listing--tours .listing__item { font-size: 19px; line-height: 26px; margin-bottom: 15px; }

  .listing--events { margin-top: 11px; }
  .listing--events .listing__item { font-size: 18.5px; line-height: 23.5px; margin-bottom: 11px; }
</style>
</head>
<body>
  <main class="card-pair">
    <section class="card card--tours" aria-label="Pedal Vista Treks tour schedule">
      <svg class="card__edge" viewBox="0 0 408 700" aria-hidden="true">
        <path d="M0 0 H92 C52 8 34 70 32 170 C30 320 26 450 34 540 C40 620 52 672 64 700 H0 Z" fill="var(--tour-blue)"/>
        <path d="M38 170 C36 320 32 450 40 540 C46 620 58 672 70 700" fill="none" stroke="var(--tour-green)" stroke-width="2.5"/>
      </svg>
      <p class="brand-name brand-name--tours">Pedal Vista<br>Treks</p>
      <div class="card__content">
        <p class="tagline tagline--tours">Fully supported bike tours.<br>Discover the hidden gems on<br>two wheels</p>
        <ul class="listing listing--tours">
          <li class="listing__item"><span class="listing__name">Heart of Colorado</span><span class="listing__detail">June 26 - July 2, 2016</span></li>
          <li class="listing__item"><span class="listing__name">Colorado Front Range Tour</span><span class="listing__detail">August 14-20, 2016</span></li>
          <li class="listing__item"><span class="listing__name">Cape Cod Tour</span><span class="listing__detail">October 9 -15, 2016</span></li>
          <li class="listing__item"><span class="listing__name">Florida Key Tours</span><span class="listing__detail">November 6-12, 2016 &amp;<br>December 4-10, 2016</span></li>
        </ul>
      </div>
    </section>

    <section class="card card--events" aria-label="KQR Venture event schedule">
      <svg class="card__edge" viewBox="0 0 408 700" aria-hidden="true">
        <path d="M0 0 H92 C52 8 34 70 32 170 C30 320 26 450 34 540 C40 620 52 672 64 700 H0 Z" fill="var(--event-red)"/>
        <path d="M38 170 C36 320 32 450 40 540 C46 620 58 672 70 700" fill="none" stroke="var(--event-blue)" stroke-width="2.5"/>
      </svg>
      <span class="brand-mark" aria-hidden="true"></span>
      <p class="brand-name brand-name--events">KQR Venture</p>
      <div class="card__content">
        <p class="tagline tagline--events">Tri Ride Series:<br>Cycling camps for youth</p>
        <ul class="listing listing--events">
          <li class="listing__item"><span class="listing__name">Mountain Bike Camp</span><span class="listing__detail">July 8-10, 2016</span></li>
          <li class="listing__item"><span class="listing__name">Cyclocross Camp</span><span class="listing__detail">August 26-28, 2016<br>Trirideseries.org</span></li>
          <li class="listing__item"><span class="listing__name">Mile High Century Ride</span><span class="listing__detail">June 18, 2016<br>Milehighcentury.com</span></li>
          <li class="listing__item"><span class="listing__name">Colorado Peak to Peak Challenge</span><span class="listing__detail">July 30, 2016 - Copeak2peak.com</span></li>
          <li class="listing__item"><span class="listing__name">Zany Wheel Ride</span><span class="listing__detail">September 11, 2016<br>zanywheelride.com</span></li>
        </ul>
      </div>
    </section>
  </main>
</body>
</html>
```